I want ideas sample designs for my book cover

Hello,

We need a book cover designed in flat and 3D Versions. We would like to have jpg and png for final output and include a copy of the PSD for future revisions.

Here are the basic details:

Title: The Harvest of Quiet Builders
Author: Norman Quillfeather

Dimensions of book:

Was looking at the Pavo website for dimensions. I thought you may want to go on there and look at the different sizes. I used the 6x9” perfect bound US trade size for my book. You will see that this has a spine width of 0.225”, Cover size of 12.48 x 9.25” and spine begins at 6.125”

If you need background info on the author just to get an idea what he does, please check:

http://NormanQuillfeather.example

IMPORTANT: Please see attached document for a more detailed info:

Exact Title Of book
Back Cover
Spine Info
Measurements of book and dimension
Examples of book covers
Norman's photo attached

Thanks,
Darlene

Industry/Entity Type

Life Coaching

Font styles to use
Serif

Requirements
Must have
• Jpg, png and PSD files
• title
• author
• exact dimensions
• front and back cover
• flat and 3d versions

```html
<!DOCTYPE html>
<html lang="en">
<head>
<meta charset="utf-8">
<title>The Harvest of Quiet Builders — Cover Spread</title>
<link href="https://fonts.googleapis.com/css2?family=PT+Sans:ital,wght@0,400;0,700;1,400&family=Oswald:wght@600&display=swap" rel="stylesheet">
<style>
  :root{
    --lime:#a5d05b;
    --navy:#29336f;
    --ink:#111318;
    --white:#ffffff;
    --photo-top:#7f9dc4;
    --photo-mid:#3c5681;
    --photo-low:#101a30;
    --portrait:#cfcfcf;
  }
  *{margin:0;padding:0;box-sizing:border-box}
  html,body{width:1200px;height:893px;overflow:hidden;background:#fff}
  .spread{position:relative;width:1200px;height:893px;font-family:"PT Sans",sans-serif;overflow:hidden}
  .back-upper{position:absolute;left:0;top:0;width:610px;height:586px;background:var(--lime)}
  .back-lower{position:absolute;left:0;top:586px;width:610px;height:307px;background:var(--navy)}
  .blurb{position:absolute;left:33px;top:38px;width:517px;color:var(--ink);font-size:13.2px;line-height:17.4px;text-align:justify;hyphens:auto}
  .blurb p{margin-bottom:17.4px}
  .author-frame{position:absolute;left:32px;top:596px;width:168px;height:168px;background:var(--lime);padding:6px}
  .author-photo{width:100%;height:100%;background:linear-gradient(135deg,#ededed,var(--portrait))}
  .bio{position:absolute;left:214px;top:592px;width:336px;color:var(--white);font-size:11.6px;line-height:14.8px;text-align:justify}
  .isbn{position:absolute;left:323px;top:782px;width:149px;height:72px;background:var(--white);font-size:8px;text-align:center;padding-top:6px;color:var(--ink)}
  .site{position:absolute;left:56px;top:816px;color:var(--white);font-size:11.5px;font-style:italic}
  .spine-title{position:absolute;left:588px;top:136px;writing-mode:vertical-rl;font-size:13px;letter-spacing:2.2px;color:var(--ink);text-transform:uppercase}
  .spine-title span{text-transform:none}
  .spine-photo{position:absolute;left:588px;top:558px;width:20px;height:26px;background:linear-gradient(#eee,#bbb)}
  .spine-author{position:absolute;left:590px;top:730px;writing-mode:vertical-rl;font-size:13px;color:var(--white)}
  .front-photo{position:absolute;left:610px;top:0;width:590px;height:893px;
    background:linear-gradient(180deg,var(--photo-top) 0%,#6f8cb6 35%,var(--photo-mid) 62%,#22355a 75%,var(--photo-low) 100%)}
  .front-kicker{position:absolute;left:610px;width:590px;top:22px;text-align:center;color:var(--lime);font-size:21px}
  .front-kicker b{font-weight:700}
  .front-author{position:absolute;left:610px;width:570px;top:62px;text-align:center;color:var(--white);font-size:38px;font-weight:700}
  .tagline{position:absolute;right:32px;top:204px;width:300px;text-align:right;color:var(--ink);font-size:24px;line-height:31.5px}
  .front-title{position:absolute;left:650px;top:550px;width:540px;height:220px}
  .front-title text{font-family:"Oswald",sans-serif;font-weight:600;fill:var(--lime)}
</style>
</head>
<body>
<div class="spread">
  <div class="back-upper"></div>
  <div class="back-lower"></div>

  <div class="blurb">
    <p>This path goes way beyond Entrepreneurism! This is a book for the awakening Entrepreneurs who are building businesses for a better world, affecting generations to come. Bringing you disruptive (in a good way) information, to turn you and your business inside-out for maximum acceleration towards your organisational vision, mission and values.</p>
    <p>There is the potential to have a more meaningful life and business by discovering the symbiotic relationship that exists between all beings. You will be empowered to take your life and business to the next level if you answer the call in this book. It will introduce you to the power of Amazonian plant medicine and other entheogens for improving relationships with yourself, your partner and your family, friends, business associates and Mother Earth.</p>
    <p>An entheogen is defined as ‘a substance (usually from a plant, but not always) that is consumed in order to alter one’s state of consciousness or to act as a catalyst towards encounters with other states of being.’ Plant medicine has been successfully used in South America for thousands of years. This ancient wisdom is helping billionaires, industry icons and entrepreneurs to be better leaders, awakening to its potential for allowing deep examination of the psyche which has the ability to heal, eliminate fears and create a new level of success both personally and professionally.</p>
    <p>Norman shares his own heart-felt personal experiences and insights gained from working with these substances and the amazing medicine men and women of the Amazon who retain thousands of years of ancient wisdom. He has spent years turning himself inside-out to powerfully transform his own life and business and wants to encourage entrepreneurs to do the same. He believes that if enough people have the opportunity to explore their own consciousness, then together we can make a positive impact on humanity. If you are ready to travel to the fringes and take a journey within, you will discover that you are the missing link you have been looking for. Get ready to expand your consciousness, transform your business and create a new inspiring lifestyle, which will benefit all beings and our beautiful Mother Earth.</p>
  </div>

  <div class="author-frame"><div class="author-photo" role="img" aria-label="Black and white portrait of the author smiling"></div></div>
  <p class="bio">Norman Quillfeather is an internationally-renowned entrepreneur, speaker, philanthropist, thought leader and best-selling author. Having played the role of transformational coach, facilitator and spoken to over three million people from twelve different countries, he challenges you in his second book to journey deep within yourself to examine the core of your true nature and how it impacts your entrepreneurial journey. Some of the world biggest game changers, social entrepreneurs, internet marketers and consultants have reported that Norman’s golden edge is to integrate “purpose with profits” in a way that brings greater meaning to the work they are doing here in the world.</p>
  <div class="isbn">ISBN</div>
  <p class="site">www.NormanQuillfeather.example</p>

  <p class="spine-title"><span>The</span> Harvest of Quiet Builders</p>
  <div class="spine-photo" role="img" aria-label="Small author portrait"></div>
  <p class="spine-author">Norman Quillfeather</p>

  <div class="front-photo" role="img" aria-label="Photo of a man in a dark suit seen from behind, looking out over the sea under a blue sky"></div>
  <p class="front-kicker">From the Best Selling Author of “<b>Lanterns</b>”</p>
  <p class="front-author">Norman Quillfeather</p>
  <p class="tagline">How this ancient wisdom is helping billionaires, industry icons and entrepreneurs to be better leaders, increase impact and leave a legacy</p>

  <svg class="front-title" viewBox="0 0 540 220" aria-label="The Harvest of Quiet Builders">
    <text x="8" y="100" font-size="62" textLength="62" lengthAdjust="spacingAndGlyphs">The</text>
    <text x="78" y="100" font-size="112" textLength="450" lengthAdjust="spacingAndGlyphs">HARVEST OF</text>
    <text x="20" y="205" font-size="112" textLength="478" lengthAdjust="spacingAndGlyphs">QUIET BUILDERS</text>
  </svg>
</div>
</body>
</html>
```